Real estate team needs a poster design to promote Free Listing competition

Need a poster design to promote a free listing competition we have about to get underway. It will run from Jan 1,2014 - June 30, 2014 (yes, I'm running late getting this piece organized :-) )! To win a free listing from us, videos need to be submitted that show why they should win the competition and get a free listing from us. It is voted on by the general public on our website. Website is currently being modified to incorporate this so it is not 'live' yet. Our team is TRHomesDirect.com.

I'd like to see designs with blue tones as a focus (our logo and branding is in blue), with some other complementary (and wow) colors incorporated. I'd like to have some depth to the poster, and like what I see with 3D text. Since the competition is about clients submitting videos a movie poster style might be appropriate.

It should be eyecatching and want people to investigate more. A catchy phrase could be 'Lights, Camera, SOLD'. Perhaps this in text in 3D, with lights shining on it, and depth behind it...?? The explanation of the contest could be 'Win the listing services of an exceptional, progressive and dynamic real estate team - a winning video is all we need'.

It should include a pointer for more information to FreeListing.TRHomesDirect.com and the date of Jan 1-June 30, 2014, or email FreeListing@TRHomesDirect.com

We would also use this same design on a A4 size postcard, and print ad.
Updates

Hi folks,

I've just uploaded a zip file of a few iterations of our team logo.  Please note though that the .eps files that I have included have the wrong blue in them.  The correct blue (which is shown in some of the .svg, jpg,.png files) is R 73, G102, B151.

Thank you all very much... looking forward to seeing what you will come up with :-)
Mira

Hello,

thank you for the entries so far.  I am liking what I am seeing.

A few thoughts.  I like the emphasis on the words 'Lights, Camera, SOLD' that I am seeing.  I am liking the incorporation of movie lighting and movie cameras as well. I also like the depth, and 3D components that I've seen in some. 

I've seen designs which have no visual of homes for sale, and some which have stock photos of homes for sale, but am now thinking that we do need some visual representation of the fact that the team sell houses.  When there are no houses in the posters then you actually have to read the text to see that we sell houses if you don't know us, but we want people to get the fact that we sell real estate immediately from first glance... so we should somehow get some visuals of houses in here also.

Some nice homes which have Images that I own, and also videos that I own, are at www.42Brenthold.com, www.8Corliss.com, www63Ashworth.com ...perhaps something of one of these can be incorporated in to give some visuals?

Thanks so much for your efforts
Mira

Hey folks,
I've just uploaded some more photos. 
With some designs that are featuring photos of houses that we have sold very prominently we perhaps should use photos of my own home instead because I am concerned about the new owners protesting about including photos of their home in the poster.  If the photo is small, or transparent it is not as much of a concern, but where it is prominent it may be more appropriate to use a photo/s where we know the owner won't complain (me :-) ).
I also added a couple of photos of the team in case you wanted to use photos of the team in your design... it is not necessary, but I'd prefer the team versus anonymous people :-)
Thanks again for all submissions... I'm so pleased with what we are getting submitted...!
Thanks
Mira 

Target Market(s)

Homeowners aged 30-55+ who are comfortable with technology. Our main demographic are well educated and have professional occupations.

Industry/Entity Type

Progressive

Requirements
Must have
• It should include a link for more information of FreeListing.TRHomesDirect.com and the date of Jan 1-June 30, 2014. Or to email FreeListing@TRHomesDirect.com
Must have our logo incorporated somewhere on the poster.
Nice to have
• Like to show depth in the poster...perhaps a background, then the 3D words of 'Lights, Camera, SOLD', and perhaps a couple of lights and movie camera in the foreground? We're open but in posters that I have seen while looking for ideas I like the ones with some depth to them.
Like blues, and blue tones with some other colors that 'pop'.
Eyecatching.
Would be great to have the explanation of the contest incorporated somewhere on the poster so that people get the idea immediately of what its all about 'Win the listing services of an exceptional, progressive and dynamic real estate team - a winning video is all we need'

```html
<!DOCTYPE html>
<html lang="en">
<head>
<meta charset="utf-8">
<title>Lights Camera Sold – TRHomesDirect.com Free Listing Competition</title>
<link rel="stylesheet" href="https://fonts.googleapis.com/css2?family=Anton&family=Oswald:wght@500;600&family=Bitter:wght@400;500&family=Open+Sans:wght@400;700&display=swap">
<style>
  :root {
    --brand-blue: #496697;
    --sky-blue: #2aa3dd;
    --night: #02060f;
    --deep-blue: #0a2a66;
    --glow-blue: #1f5fc4;
    --white: #ffffff;
    --shade: #1c2d4a;
  }
  html, body {
    margin: 0;
    padding: 0;
    width: 927px;
    height: 1200px;
    overflow: hidden;
    background: var(--white);
  }
  .poster {
    position: relative;
    width: 927px;
    height: 1200px;
    overflow: hidden;
    background: var(--white);
  }

  /* Header / brand */
  .brand {
    position: absolute;
    top: 18px;
    left: 0;
    width: 100%;
    display: flex;
    justify-content: center;
    align-items: center;
    gap: 14px;
  }
  .brand-mark {
    width: 62px;
    height: 62px;
    background: var(--brand-blue);
  }
  .brand-text { display: flex; flex-direction: column; }
  .brand-name {
    font-family: "Open Sans", sans-serif;
    font-weight: 700;
    font-size: 34px;
    line-height: 1;
    color: var(--brand-blue);
    letter-spacing: -0.5px;
  }
  .brand-tagline {
    font-family: "Open Sans", sans-serif;
    font-weight: 400;
    font-size: 19px;
    color: var(--brand-blue);
    margin-top: 6px;
  }

  /* Stage background */
  .stage {
    position: absolute;
    left: 0;
    top: 100px;
    width: 927px;
    height: 1100px;
  }

  /* Headline */
  .headline {
    position: absolute;
    top: 300px;
    left: 0;
    width: 100%;
    margin: 0;
    text-align: center;
    font-family: "Anton", sans-serif;
    font-weight: 400;
    color: var(--white);
    text-transform: uppercase;
  }
  .headline span {
    display: block;
    transform-origin: center top;
    text-shadow:
      2px 2px 0 #c9d3e3,
      4px 4px 0 #9aa9c2,
      6px 6px 0 #6f7f9c,
      8px 8px 0 #4c5b78,
      10px 10px 0 var(--shade),
      14px 16px 24px rgba(0,0,0,0.7);
  }
  .headline .lights { font-size: 188px; line-height: 1; transform: scaleY(1.02); letter-spacing: 2px; }
  .headline .camera { font-size: 158px; line-height: 0.98; margin-top: -10px; transform: scaleY(1.0); letter-spacing: 1px; }
  .headline .sold { font-size: 232px; line-height: 0.95; margin-top: -14px; letter-spacing: 4px; }

  /* Contest details */
  .pitch {
    position: absolute;
    top: 918px;
    left: 0;
    width: 100%;
    margin: 0;
    text-align: center;
    font-family: "Oswald", sans-serif;
    font-weight: 600;
    font-size: 39px;
    line-height: 45px;
    color: var(--white);
    text-transform: uppercase;
    letter-spacing: 0.3px;
  }
  .slogan {
    position: absolute;
    top: 1018px;
    left: 0;
    width: 100%;
    margin: 0;
    text-align: center;
    font-family: "Bitter", serif;
    font-weight: 400;
    font-size: 46px;
    color: var(--sky-blue);
    letter-spacing: 0.5px;
  }
  .dates {
    position: absolute;
    top: 1088px;
    left: 0;
    width: 100%;
    display: flex;
    align-items: center;
    justify-content: center;
    gap: 20px;
  }
  .dates .rule {
    height: 3px;
    width: 175px;
    background: linear-gradient(90deg, rgba(255,255,255,0), var(--white));
  }
  .dates .rule.right {
    background: linear-gradient(90deg, var(--white), rgba(255,255,255,0));
  }
  .dates .range {
    font-family: "Bitter", serif;
    font-weight: 500;
    font-size: 32px;
    color: var(--white);
  }
  .contact {
    position: absolute;
    top: 1138px;
    left: 0;
    width: 100%;
    text-align: center;
    font-family: "Bitter", serif;
    font-size: 24px;
    color: var(--sky-blue);
  }
</style>
</head>
<body>
<main class="poster">

  <header class="brand">
    <div class="brand-mark"></div>
    <div class="brand-text">
      <div class="brand-name">TRHomesDirect.com</div>
      <div class="brand-tagline">A Data Driven approach to real estate</div>
    </div>
  </header>

  <svg class="stage" viewBox="0 0 927 1100" role="img" aria-label="Stadium floodlights shining down onto a glowing blue tiled stage">
    <defs>
      <linearGradient id="stageFade" x1="0" y1="0" x2="0" y2="1">
        <stop offset="0" stop-color="#0b1f4a"/>
        <stop offset="0.35" stop-color="#0d3478"/>
        <stop offset="0.7" stop-color="#071a3d"/>
        <stop offset="1" stop-color="#02060f"/>
      </linearGradient>
      <radialGradient id="glowLeft" cx="0.15" cy="0.12" r="0.45">
        <stop offset="0" stop-color="#e8f4ff" stop-opacity="0.95"/>
        <stop offset="0.3" stop-color="#5fa2ff" stop-opacity="0.55"/>
        <stop offset="1" stop-color="#1f5fc4" stop-opacity="0"/>
      </radialGradient>
      <radialGradient id="glowRight" cx="0.85" cy="0.12" r="0.45">
        <stop offset="0" stop-color="#e8f4ff" stop-opacity="0.95"/>
        <stop offset="0.3" stop-color="#5fa2ff" stop-opacity="0.55"/>
        <stop offset="1" stop-color="#1f5fc4" stop-opacity="0"/>
      </radialGradient>
      <radialGradient id="glowCenter" cx="0.5" cy="0.1" r="0.3">
        <stop offset="0" stop-color="#d6ebff" stop-opacity="0.8"/>
        <stop offset="1" stop-color="#1f5fc4" stop-opacity="0"/>
      </radialGradient>
      <radialGradient id="floorGlow" cx="0.5" cy="0.5" r="0.5">
        <stop offset="0" stop-color="#3f86e6" stop-opacity="0.6"/>
        <stop offset="1" stop-color="#0a2a66" stop-opacity="0"/>
      </radialGradient>
    </defs>
    <path d="M0 30 Q463 -20 927 30 L927 1100 L0 1100 Z" fill="url(#stageFade)"/>
    <ellipse cx="463" cy="560" rx="480" ry="300" fill="url(#floorGlow)"/>
    <path d="M0 30 Q463 -20 927 30 L927 1100 L0 1100 Z" fill="url(#glowLeft)"/>
    <path d="M0 30 Q463 -20 927 30 L927 1100 L0 1100 Z" fill="url(#glowRight)"/>
    <path d="M0 30 Q463 -20 927 30 L927 1100 L0 1100 Z" fill="url(#glowCenter)"/>
    <rect x="0" y="800" width="927" height="300" fill="#02060f" opacity="0.75"/>
  </svg>

  <h1 class="headline">
    <span class="lights">Lights</span>
    <span class="camera">Camera</span>
    <span class="sold">Sold</span>
  </h1>

  <p class="pitch">Win the listing services of an exceptional<br>progressive and dynamic real estate team</p>
  <p class="slogan">a winning video is all we need</p>

  <div class="dates">
    <span class="rule"></span>
    <span class="range">Jan 1-June 30, 2014</span>
    <span class="rule right"></span>
  </div>

  <div class="contact">FreeListing@TRHomesDirect.com</div>

</main>
</body>
</html>
```